Calvanto Group Real Estate Company business cards

New business card design, we are generally happy with the basic layout of the existing front of business card, (feel free to change) but require a head shot photo on the back side.

http://www.calvanto.com.au/

Attached logos, and existing business card

------------------------------

Target Market(s)

Real estate

Industry/Entity Type

Real Estate

Contact Information for Business Card

Standard size double sided

Font styles to use
Other font styles liked:
• Futura

Requirements
Must have
• Photo head shot on the back side
Nice to have
• yes
Should not have
• No

```html
<!DOCTYPE html>
<html lang="en">
<head>
<meta charset="utf-8">
<title>Calvanto Group business cards</title>
<link href="https://fonts.googleapis.com/css2?family=Open+Sans:wght@400;600&family=Roboto+Condensed:wght@500&display=swap" rel="stylesheet">
<style>
  :root {
    --backdrop: #3b3b3b;
    --card: #fbfbfb;
    --ink: #2d2461;
    --accent: #f39019;
    --text: #4a4a4a;
    --rule: #cfcfcf;
    --photo-light: #eef0f4;
    --photo-dark: #27345f;
  }
  * { box-sizing: border-box; margin: 0; padding: 0; }
  html, body { width: 1200px; height: 750px; overflow: hidden; }
  body {
    background: var(--backdrop);
    font-family: "Open Sans", Arial, sans-serif;
    position: relative;
  }
  .card {
    position: absolute;
    top: 228px;
    width: 462px;
    height: 262px;
    background: var(--card);
    overflow: hidden;
  }
  .card--front { left: 124px; }
  .card--back { left: 618px; }

  .wordmark {
    position: absolute;
    color: var(--ink);
    font-weight: 600;
    letter-spacing: -0.5px;
    line-height: 1;
  }
  .tagline {
    position: absolute;
    font-family: "Roboto Condensed", Arial, sans-serif;
    font-weight: 500;
    font-size: 12px;
    color: var(--ink);
    white-space: nowrap;
  }
  .tagline .sep { margin: 0 7px; }

  .card--front .wordmark { left: 32px; top: 110px; font-size: 36px; }
  .card--front .tagline { left: 75px; top: 157px; }

  .divider {
    position: absolute;
    left: 229px; top: 74px;
    width: 1px; height: 128px;
    background: var(--rule);
  }
  .details { position: absolute; left: 248px; top: 68px; color: var(--text); }
  .details .name { font-size: 18px; font-weight: 600; color: var(--ink); line-height: 22px; }
  .details .role { font-size: 13px; color: var(--accent); line-height: 16px; }
  .details .company { margin-top: 8px; font-size: 13px; font-weight: 600; line-height: 17px; }
  .details .abn { font-size: 12px; line-height: 17px; }
  .contacts { list-style: none; margin-top: 4px; }
  .contacts li { display: flex; align-items: center; font-size: 12px; line-height: 18px; }
  .contacts svg { width: 11px; height: 11px; margin-right: 7px; fill: var(--ink); }

  .card--back .wordmark { left: 30px; top: 158px; font-size: 36px; }
  .card--back .tagline { left: 75px; top: 207px; }
  .card--back .website {
    position: absolute; left: 28px; top: 225px;
    font-size: 12px; letter-spacing: 3px; color: var(--text);
  }
  .headshot {
    position: absolute; left: 278px; top: 12px;
    width: 176px; height: 250px;
    background: linear-gradient(180deg, var(--photo-light) 0%, var(--photo-light) 35%, var(--photo-dark) 60%, var(--photo-dark) 100%);
  }
</style>
</head>
<body>
  <section class="card card--front">
    <div class="wordmark">calvanto</div>
    <div class="tagline">Buy<span class="sep">I</span>Sell<span class="sep">I</span>Rent</div>
    <div class="divider"></div>
    <div class="details">
      <div class="name">Daniel Tran</div>
      <div class="role">Director</div>
      <div class="company">Calvanto Group</div>
      <div class="abn">ABN: 12 345 678 901</div>
      <ul class="contacts">
        <li><svg viewBox="0 0 24 24"><path d="M6.6 10.8a15.1 15.1 0 0 0 6.6 6.6l2.2-2.2a1 1 0 0 1 1-.25 11.4 11.4 0 0 0 3.6.57 1 1 0 0 1 1 1V20a1 1 0 0 1-1 1A17 17 0 0 1 3 4a1 1 0 0 1 1-1h3.5a1 1 0 0 1 1 1c0 1.25.2 2.45.57 3.57a1 1 0 0 1-.25 1z"/></svg>0400 555 218</li>
        <li><svg viewBox="0 0 24 24"><path d="M2 5h20v14H2z M2 5l10 8 10-8" fill="none" stroke="#2d2461" stroke-width="2.5"/></svg>daniel.tran@calvanto.com.au</li>
        <li><svg viewBox="0 0 24 24"><circle cx="12" cy="12" r="10"/><path d="M8 6c2 1 1 3 3 4s1 3-1 3-2 3 0 5M16 5c-1 2 1 3 3 3M15 14c1 1 3 1 3 3" fill="none" stroke="#fbfbfb" stroke-width="1.6"/></svg>www.calvanto.com.au</li>
      </ul>
    </div>
  </section>

  <section class="card card--back">
    <div class="wordmark">calvanto</div>
    <div class="tagline">Buy<span class="sep">I</span>Sell<span class="sep">I</span>Rent</div>
    <div class="website">www.calvanto.com.au</div>
    <div class="headshot" role="img" aria-label="Head shot photo of the director in a navy suit and blue tie"></div>
  </section>
</body>
</html>
```